Building company buisness cards

We are looking for a sharp modern new look for our business cards.
We are a New Zealand based company that specialises in house and land packages.
We have attached a photo of the current logo and would like to see if it can be improved somehow if needed.
We are open to any colours but we have chosen green at this stage.
Feel free to change the font and make the logo smarter looking.
Play with the colours and see what looks best.

We want a card that looks so good know one will want to throw it away!

Target Market(s)

Home buyers

Industry/Entity Type

Building

Contact Information for Business Card

Derek Tolvane
0217394062
dtolvane@quillmarkhomesteads.co.nz
quillmarkhomesteads.co.nz

Font styles to use
Serif
Sans Serif

Colors

Designer to choose colors to be used in the design.

Requirements
Must have
• Logo and company name on one side, details on the other side
Nice to have
• Color codes for the original green are HEX #4a8028, RGB(74,128,40), CMYK(42,0,69,50)
• Round corners, Raised and/or spot UV

```html
<!DOCTYPE html>
<html lang="en">
<head>
<meta charset="utf-8">
<title>Quillmark Homesteads – Business Cards</title>
<link href="https://fonts.googleapis.com/css2?family=Source+Sans+3:wght@400;600;700;800&family=Arimo:wght@700&display=swap" rel="stylesheet">
<style>
  :root {
    --brand-green: #4e8722;
    --brand-green-soft: #dbe6d3;
    --paper: #ffffff;
    --ink: #2b2b2b;
    --backdrop: #c8c9cb;
  }
  * { margin: 0; padding: 0; box-sizing: border-box; }
  html, body { width: 1200px; height: 1015px; overflow: hidden; }
  body {
    background: var(--backdrop);
    font-family: "Source Sans 3", Arial, sans-serif;
    position: relative;
  }
  .card {
    position: absolute;
    width: 687px;
    height: 393px;
    overflow: hidden;
    box-shadow: 0 3px 6px rgba(0,0,0,0.22);
  }

  /* Front: contact side */
  .card-front {
    left: 424px; top: 90px;
    background: var(--paper);
    border-radius: 22px;
    border: 1px solid #555;
  }
  .front-brand {
    position: absolute;
    left: 30px; top: 60px;
    width: 300px;
    text-align: center;
    color: var(--brand-green);
    font-weight: 800;
    line-height: 1;
  }
  .brand-mark-square {
    display: block;
    width: 30px; height: 30px;
    margin: 0 auto 18px;
    background: var(--brand-green);
  }
  .front-brand .brand-line-1 { font-size: 24px; letter-spacing: 0.5px; }
  .front-brand .brand-line-2 { font-size: 37px; margin-top: 4px; }
  .front-rule {
    position: absolute;
    left: 109px; top: 192px;
    width: 120px; height: 2px;
    background: var(--brand-green);
  }
  .person {
    position: absolute;
    right: 27px; top: 58px;
    text-align: right;
    font-family: "Arimo", Arial, sans-serif;
    font-weight: 700;
    line-height: 1.22;
  }
  .person-name { color: var(--brand-green); font-size: 26px; }
  .person-title { color: var(--ink); font-size: 26px; }
  .contact-band {
    position: absolute;
    left: 0; bottom: 0;
    width: 100%; height: 144px;
    background: var(--brand-green);
  }
  .band-window {
    position: absolute;
    left: 477px; top: 249px;
    width: 160px; height: 113px;
    background: var(--paper);
  }
  .contact-list {
    position: absolute;
    left: 37px; top: 276px;
    list-style: none;
    color: var(--paper);
  }
  .contact-list li {
    display: flex;
    align-items: center;
    height: 32px;
    font-size: 18px;
    letter-spacing: -0.2px;
  }
  .contact-list li.phone { font-size: 19px; letter-spacing: 0.3px; }
  .contact-list svg { width: 18px; height: 18px; margin-right: 9px; flex: none; }

  /* Back: brand side */
  .card-back {
    left: 102px; top: 549px;
    background: var(--brand-green);
    border-radius: 40px;
  }
  .back-brand {
    position: absolute;
    left: 0; top: 72px;
    width: 100%;
    text-align: center;
    color: var(--paper);
    font-weight: 800;
    line-height: 1;
  }
  .back-brand .brand-mark-square {
    width: 44px; height: 44px;
    margin-bottom: 38px;
    background: var(--paper);
  }
  .back-brand .brand-line-1 { font-size: 34px; letter-spacing: 0.5px; }
  .back-brand .brand-line-2 { font-size: 50px; margin-top: 6px; }
  .back-rule {
    position: absolute;
    left: 249px; top: 274px;
    width: 162px; height: 2px;
    background: var(--paper);
  }
  .back-url {
    position: absolute;
    left: 0; top: 344px;
    width: 100%;
    text-align: center;
    color: var(--paper);
    font-size: 17px;
    letter-spacing: 2.4px;
  }
</style>
</head>
<body>

  <section class="card card-front" aria-label="Business card front">
    <div class="front-brand">
      <span class="brand-mark-square"></span>
      <div class="brand-line-1">quillmark</div>
      <div class="brand-line-2">homesteads.</div>
    </div>
    <div class="front-rule"></div>

    <div class="person">
      <div class="person-name">Derek Tolvane</div>
      <div class="person-title">Title</div>
    </div>

    <div class="contact-band"></div>
    <div class="band-window"></div>

    <ul class="contact-list">
      <li class="phone">
        <svg viewBox="0 0 20 20" aria-hidden="true"><circle cx="10" cy="10" r="8.5" fill="none" stroke="#fff" stroke-width="1.4"/><path d="M7.2 5.5c.6-.3 1.1 0 1.3.5l.6 1.5c.2.5 0 .9-.4 1.1l-.5.3c.4 1.3 1.2 2.3 2.3 3l.5-.4c.4-.3.9-.3 1.2.1l1 1.2c.3.4.2 1-.2 1.3-1.5 1-3.4.3-4.9-1.4S5.8 6.4 7.2 5.5z" fill="#fff"/></svg>
        0217394062
      </li>
      <li>
        <svg viewBox="0 0 20 20" aria-hidden="true"><path d="M2 8l8-5 8 5v8H2z" fill="#fff"/><path d="M2 8l8 5 8-5" fill="none" stroke="#4e8722" stroke-width="1.3"/></svg>
        dtolvane@quillmarkhomesteads.co.nz
      </li>
      <li>
        <svg viewBox="0 0 20 20" aria-hidden="true" fill="none" stroke="#fff" stroke-width="1.2"><circle cx="10" cy="10" r="8"/><ellipse cx="10" cy="10" rx="3.5" ry="8"/><path d="M2 10h16M3.2 6h13.6M3.2 14h13.6"/></svg>
        www.quillmarkhomesteads.co.nz
      </li>
    </ul>
  </section>

  <section class="card card-back" aria-label="Business card back">
    <div class="back-brand">
      <span class="brand-mark-square"></span>
      <div class="brand-line-1">quillmark</div>
      <div class="brand-line-2">homesteads.</div>
    </div>
    <div class="back-rule"></div>
    <div class="back-url">www.quillmarkhomesteads.co.nz</div>
  </section>

</body>
</html>
```